Law firm business card

Information:

Me Mireille Dufontaine

website: dufontaine-legal.ca
email: mireille@dufontaine-legal.ca
Phone: 514 382-5167
Fax: 514 382-5169

Address:
Dufontaine and associates
2719 Belcourtier
Montreal, QC
H2K 3M9

Areas of Expertise:
Franchise Agreements, Financing, Acquisition, Real Estate Development, Commercial Agreements and Corporate Law

Target Market(s)

executives, companie managers

Industry/Entity Type

Business

Colors
f78f20
000000

Requirements
Must have
• Must use the logo, the logo is available here:

https://www.filecrate-example.com/sh/qyt3kwud82mfa0x/BBQTn7Lhvpe_kRTXwJM_GhcYb

```html
<!DOCTYPE html>
<html lang="en">
<head>
<meta charset="utf-8">
<title>Dufontaine &amp; Associates — Stationery</title>
<link href="https://fonts.googleapis.com/css2?family=Cinzel:wght@400;600&family=Lato:wght@400;700&family=Pinyon+Script&display=swap" rel="stylesheet">
<style>
  :root {
    --orange: #f78f20;
    --black: #000000;
    --ink: #2b2b2b;
    --grey: #555555;
    --rule: #cfcfcf;
    --paper: #ffffff;
    --backdrop: #c8d6de;
  }
  * { margin: 0; padding: 0; box-sizing: border-box; }
  html, body { width: 1200px; height: 930px; overflow: hidden; }
  body { background: var(--backdrop); position: relative; font-family: "Lato", Arial, sans-serif; }

  .letterhead, .card { position: absolute; background: var(--paper); box-shadow: 0 2px 6px rgba(0,0,0,.25); overflow: hidden; }
  .letterhead { left: 40px; top: 30px; width: 673px; height: 870px; }

  .brand { position: absolute; display: flex; align-items: center; }
  .brand-circle { flex: none; border-radius: 50%; }
  .brand-divider { flex: none; width: 1px; align-self: stretch; }
  .brand-name { font-family: "Cinzel", Georgia, serif; font-weight: 600; line-height: 1; white-space: nowrap; }
  .brand-name .line1, .brand-name .line2 { display: block; }

  .letterhead .brand { left: 73px; top: 33px; }
  .letterhead .brand-circle { width: 57px; height: 57px; border: 3px solid var(--orange); margin-right: 12px; }
  .letterhead .brand-divider { background: var(--grey); margin-right: 12px; }
  .letterhead .brand-name .line1 { font-size: 24px; color: var(--orange); }
  .letterhead .brand-name .line2 { font-size: 13px; letter-spacing: 1.5px; margin-top: 3px; text-align: center; color: var(--grey); }

  .contact { position: absolute; list-style: none; font-family: "Cinzel", Georgia, serif; color: var(--grey); white-space: nowrap; }
  .contact li { display: flex; align-items: center; }
  .contact svg { width: 10px; height: 10px; margin-right: 6px; fill: var(--orange); flex: none; }
  .letterhead .contact { left: 438px; top: 37px; font-size: 11px; line-height: 12.6px; }

  .watermark { position: absolute; left: 205px; top: 290px; width: 300px; height: 300px; border-radius: 50%; border: 26px solid var(--orange); opacity: .12; }

  .letter { position: absolute; left: 73px; top: 198px; width: 527px; color: var(--ink); font-size: 11px; line-height: 12.5px; text-align: justify; }
  .letter .salutation { font-weight: 700; font-size: 11px; margin-bottom: 8px; }
  .letter p { margin-bottom: 12.5px; }
  .letter .signoff { margin-top: 24px; margin-bottom: 4px; }
  .letter .signature { font-family: "Pinyon Script", cursive; font-size: 26px; line-height: 30px; color: var(--black); text-align: left; font-weight: 400; }

  .footer-rule { position: absolute; left: 0; right: 0; height: 3px; background: var(--orange); }
  .footer-band { position: absolute; left: 0; right: 0; background: var(--black); color: #fff; font-family: "Cinzel", Georgia, serif; display: flex; align-items: center; justify-content: center; white-space: nowrap; }
  .letterhead .footer-rule { top: 828px; }
  .letterhead .footer-band { top: 836px; height: 34px; font-size: 12.5px; letter-spacing: .4px; }

  .card { width: 408px; height: 230px; }
  .card-front { left: 757px; top: 138px; background: var(--black); }
  .card-front .brand { left: 58px; top: 78px; }
  .card-front .brand-circle { width: 66px; height: 66px; border: 3px solid #fff; margin-right: 14px; }
  .card-front .brand-divider { background: #bbbbbb; margin-right: 12px; }
  .card-front .brand-name { color: #fff; }
  .card-front .brand-name .line1 { font-size: 26px; }
  .card-front .brand-name .line2 { font-size: 15px; letter-spacing: 1.5px; margin-top: 3px; text-align: center; }

  .card-back { left: 757px; top: 436px; }
  .card-back .mark { position: absolute; left: 40px; top: 52px; width: 106px; height: 106px; border-radius: 50%; border: 4px solid var(--orange); }
  .card-back .divider { position: absolute; left: 190px; top: 28px; width: 1px; height: 160px; background: var(--rule); }
  .card-back .holder { position: absolute; left: 205px; top: 36px; font-family: "Cinzel", Georgia, serif; color: var(--orange); font-size: 12px; font-weight: 600; line-height: 14px; white-space: nowrap; }
  .card-back .address { position: absolute; left: 205px; top: 63px; font-family: "Cinzel", Georgia, serif; color: var(--grey); font-size: 10px; line-height: 11.6px; font-style: normal; white-space: nowrap; }
  .card-back .contact { left: 205px; top: 124px; font-size: 9.5px; line-height: 11.6px; }
  .card-back .footer-rule { top: 207px; height: 2px; }
  .card-back .footer-band { top: 212px; height: 18px; }
</style>
</head>
<body>
  <svg width="0" height="0" style="position:absolute" aria-hidden="true">
    <defs>
      <symbol id="icon-phone" viewBox="0 0 10 10"><path d="M1 3.5C1 2.3 2.5 1.5 5 1.5S9 2.3 9 3.5L7.5 4.2 6.8 3.2H3.2L2.5 4.2Z M2.6 5h4.8l1 3.5H1.6Z"/></symbol>
      <symbol id="icon-fax" viewBox="0 0 10 10"><path d="M2.5 1h5v2.5h-5z M1 4h8v4H7.5v1h-5V8H1z M3.5 6.5h3v1.5h-3z" fill-rule="evenodd"/></symbol>
      <symbol id="icon-mail" viewBox="0 0 10 10"><path d="M.5 2h9v6h-9z M1.2 2.6 5 5.5 8.8 2.6v-.1H1.2z" fill-rule="evenodd"/></symbol>
      <symbol id="icon-web" viewBox="0 0 10 10"><path d="M5 .5a4.5 4.5 0 1 0 0 9 4.5 4.5 0 0 0 0-9zm0 1c.6 0 1.3 1.2 1.5 3H3.5C3.7 2.7 4.4 1.5 5 1.5zM1.6 5.5h1.9c.1 1.1.4 2 .8 2.7A3.5 3.5 0 0 1 1.6 5.5zm0-1a3.5 3.5 0 0 1 2.7-2.7c-.4.7-.7 1.6-.8 2.7zm4.9 1c-.2 1.8-.9 3-1.5 3s-1.3-1.200-1.5-3zm.2 2.7c.4-.7.7-1.6.8-2.7h1.9a3.5 3.5 0 0 1-2.7 2.7zm.8-3.7c-.1-1.1-.4-2-.8-2.7a3.5 3.5 0 0 1 2.7 2.7z"/></symbol>
    </defs>
  </svg>

  <section class="letterhead" aria-label="Letterhead">
    <div class="brand">
      <span class="brand-circle"></span>
      <span class="brand-divider"></span>
      <span class="brand-name"><span class="line1">DUFONTAINE</span><span class="line2">&amp; ASSOCIATES</span></span>
    </div>
    <ul class="contact">
      <li><svg><use href="#icon-phone"/></svg>514 382 5167</li>
      <li><svg><use href="#icon-fax"/></svg>514 382 5169</li>
      <li><svg><use href="#icon-mail"/></svg>MIREILLE@DUFONTAINE-LEGAL.CA</li>
      <li><svg><use href="#icon-web"/></svg>WWW.DUFONTAINE-LEGAL.CA</li>
    </ul>

    <div class="watermark" aria-hidden="true"></div>

    <div class="letter">
      <p class="salutation">Dear John Doe,</p>
      <p>Lorem ipsum dolor sit amet, consectetuer adipiscing elit, sed diam nonummy nibh euismod tincidunt ut laoreet dolore magna aliquam erat volutpat. Ut wisi enim ad minim veniam, quis nostrud exerci tation ullamcorper suscipit lobortis nisl ut aliquip ex ea commodo consequat. Duis autem vel eum iriure dolor in hendrerit in vulputate velit esse molestie consequat, vel illum dolore eu feugiat nulla facilisis at vero eros et accumsan et iusto odio dignissim qui blandit praesent luptatum zzril delenit augue duis dolore te feugait nulla facilisi. Nam liber tempor cum soluta nobis eleifend option congue nihil imperdiet doming id quod mazim placerat facer possim assum. Typi non habent claritatem insitam; est usus legentis in iis qui facit eorum vel illum dolore eu feugiat nulla claritatem.</p>
      <p>Investigationes demonstraverunt lectores legere me lius quod ii legunt saepius. Claritas est etiam processus dynamicus, qui sequitur mutationem consuetudium lectorum. Mirum est notare quam littera gothica, quam nunc putamus parum claram, anteposuerit litterarum formas humanitatis per seacula quarta decima et quinta decima. Eodem modo typi, qui nunc nobis videntur parum clari, fiant sollemnes in futurum.</p>
      <p>Lorem ipsum dolor sit amet, consectetuer adipiscing elit, sed diam nonummy nibh euismod tincidunt ut laoreet dolore magna aliquam erat volutpat. Ut wisi enim ad minim veniam, quis nostrud exerci tation ullamcorper suscipit lobortis nisl ut aliquip ex ea commodo consequat. Duis autem vel eum iriure dolor in hendrerit in vulputate velit esse molestie consequat, vel illum dolore eu feugiat nulla facilisis at vero eros et accumsan et iusto odio dignissim qui blandit praesent luptatum zzril delenit augue duis dolore te feugait nulla facilisi. Nam liber tempor cum soluta nobis eleifend option congue nihil imperdiet doming id quod mazim placerat facer possim assum. Typi non habent claritatem insitam; est usus legentis in iis qui facit eorum vel illum dolore eu feugiat nulla claritatem.</p>
      <p>Duis autem vel eum iriure dolor in hendrerit in vulputate velit esse molestie consequat, vel illum dolore eu feugiat nulla facilisis at vero eros et accumsan et iusto odio dignissim qui blandit praesent luptatum zzril delenit augue duis dolore te feugait nulla facilisi. Nam liber tempor cum soluta nobis eleifend option congue nihil imperdiet doming id quod mazim placerat facer possim assum.</p>
      <p class="signoff">Your Sincerely,</p>
      <p class="signature">Laurent Bessette</p>
    </div>

    <div class="footer-rule"></div>
    <div class="footer-band">Dufontaine and associates, 2719 Belcourtier, Montreal, QC, H2K 3M9</div>
  </section>

  <section class="card card-front" aria-label="Business card front">
    <div class="brand">
      <span class="brand-circle"></span>
      <span class="brand-divider"></span>
      <span class="brand-name"><span class="line1">DUFONTAINE</span><span class="line2">&amp; ASSOCIATES</span></span>
    </div>
  </section>

  <section class="card card-back" aria-label="Business card back">
    <div class="mark" aria-hidden="true"></div>
    <div class="divider"></div>
    <h1 class="holder">Me Mireille Dufontaine</h1>
    <address class="address">Dufontaine and associates<br>2719 Belcourtier<br>Montreal, QC<br>H2K 3M9</address>
    <ul class="contact">
      <li><svg><use href="#icon-phone"/></svg>514 382 5167</li>
      <li><svg><use href="#icon-fax"/></svg>514 382 5169</li>
      <li><svg><use href="#icon-mail"/></svg>mireille@dufontaine-legal.ca</li>
      <li><svg><use href="#icon-web"/></svg>www.dufontaine-legal.ca</li>
    </ul>
    <div class="footer-rule"></div>
    <div class="footer-band"></div>
  </section>
</body>
</html>
```